Business Card Design

I already have a company logo for my company. I have a logo for the manufacturer we represent. I want a professional business card design.

```html
<!DOCTYPE html>
<html lang="en">
<head>
<meta charset="utf-8">
<title>Beacon Alert Group – Business Card</title>
<link href="https://fonts.googleapis.com/css2?family=Open+Sans:wght@400;600;700&display=swap" rel="stylesheet">
<style>
  :root {
    --stage: #2b2e33;
    --card-white: #ffffff;
    --card-black: #141414;
    --brand-red: #e3262d;
    --brand-gold: #d4a017;
    --ink: #2a2a2a;
  }
  * { box-sizing: border-box; margin: 0; padding: 0; }
  html, body {
    width: 1200px; height: 900px; overflow: hidden;
    background: var(--stage);
    font-family: "Open Sans", Arial, sans-serif;
  }
  .stage {
    width: 1200px; height: 900px;
    display: flex; align-items: center; justify-content: center; gap: 40px;
  }
  .card {
    position: relative;
    width: 540px; height: 309px;
    border-radius: 22px;
    overflow: hidden;
  }
  .card--front { background: var(--card-white); }
  .card--back { background: var(--card-black); display: flex; align-items: center; justify-content: center; }

  .sweep { position: absolute; inset: 0; width: 100%; height: 100%; }

  .wordmark {
    display: flex; align-items: center; gap: 10px;
    font-weight: 700; font-size: 22px; letter-spacing: 1px;
    color: var(--brand-red); text-transform: uppercase;
  }
  .wordmark__square { width: 26px; height: 26px; background: var(--brand-gold); }
  .card--front .wordmark { position: absolute; top: 46px; left: 190px; }
  .card--back .wordmark { font-size: 28px; }

  .holder { position: absolute; left: 48px; top: 128px; }
  .holder__name { color: var(--brand-red); font-weight: 600; font-size: 22px; line-height: 1.2; white-space: nowrap; }
  .holder__title { color: var(--ink); font-size: 12.5px; margin-top: 2px; white-space: nowrap; }

  .divider { position: absolute; left: 212px; top: 130px; width: 2px; height: 62px; background: var(--brand-gold); }

  .contacts { position: absolute; left: 226px; top: 128px; list-style: none; }
  .contacts li { display: flex; align-items: center; gap: 8px; font-size: 12.5px; color: var(--ink); height: 22px; white-space: nowrap; }
  .contacts svg { width: 12px; height: 12px; flex: none; }
</style>
</head>
<body>
<main class="stage">
  <section class="card card--front" aria-label="Card front">
    <svg class="sweep" viewBox="0 0 540 309" aria-hidden="true">
      <path d="M10 40 C 14 200, 60 270, 525 303" fill="none" stroke="var(--brand-red)" stroke-width="2.5"/>
    </svg>
    <div class="wordmark"><span class="wordmark__square"></span>Beacon Alert Group</div>
    <div class="holder">
      <p class="holder__name">Daniel Reyes</p>
      <p class="holder__title">Managing Director</p>
    </div>
    <div class="divider"></div>
    <ul class="contacts">
      <li><svg viewBox="0 0 12 12"><circle cx="6" cy="6" r="6" fill="var(--brand-red)"/><path d="M4 3.2 L5 3 L5.6 4.6 L4.9 5.1 Q5.4 6.4 6.9 7.1 L7.4 6.4 L9 7 L8.8 8 Q6.5 8.8 4.2 6.3 Q3 4.5 4 3.2Z" fill="#fff"/></svg>555.210.0147</li>
      <li><svg viewBox="0 0 12 12"><circle cx="6" cy="6" r="6" fill="var(--brand-red)"/><rect x="3" y="4" width="6" height="4.2" fill="#fff"/><path d="M3 4 L6 6.3 L9 4" fill="none" stroke="var(--brand-red)" stroke-width="0.8"/></svg>info@beaconalertgroup.com</li>
      <li><svg viewBox="0 0 12 12"><circle cx="6" cy="6" r="6" fill="var(--brand-red)"/><circle cx="6" cy="6" r="3" fill="none" stroke="#fff" stroke-width="0.9"/><path d="M3 6 H9 M6 3 Q4.5 6 6 9 M6 3 Q7.5 6 6 9" fill="none" stroke="#fff" stroke-width="0.7"/></svg>www.beaconalertgroup.com</li>
    </ul>
  </section>

  <section class="card card--back" aria-label="Card back">
    <div class="wordmark"><span class="wordmark__square"></span>Beacon Alert Group</div>
  </section>
</main>
</body>
</html>
```